Business Card and Simple Logo Desgin

New Zealand based start up company "Vesta Advisory LTD" requires business cards and simple logo design.

Card Content.

Vesta Advisory LTD

Rebecca Thornbury
CA, BMS (Hons)

r.thornbury@vestaadvisory.co.nz
PH +64 21 574 613

Target Market(s)

Corporate Business in IT, Finance and accounting.

Industry/Entity Type

Business

```html
<!DOCTYPE html>
<html lang="en">
<head>
<meta charset="utf-8">
<title>Vesta Advisory LTD — Business Card</title>
<link href="https://fonts.googleapis.com/css2?family=PT+Sans:wght@400;700&display=swap" rel="stylesheet">
<style>
  :root {
    --page-bg: #2a2a2a;
    --card-white: #ffffff;
    --card-grey: #e6e7e8;
    --band-light: #c3dbe3;
    --band-deep: #93b3bd;
    --brand-bronze: #8a5a1c;
    --text-main: #555a5e;
    --text-soft: #4a4f53;
    --band-text: #3a3d40;
    --dot-fill: #f4f8f9;
  }
  * { margin: 0; padding: 0; box-sizing: border-box; }
  html, body {
    width: 1200px;
    height: 900px;
    overflow: hidden;
    background: var(--page-bg);
    font-family: "PT Sans", "Myriad Pro", sans-serif;
  }
  .canvas {
    position: relative;
    width: 1200px;
    height: 900px;
    display: flex;
    align-items: center;
    justify-content: center;
  }
  .business-card {
    position: relative;
    width: 840px;
    height: 480px;
    border-radius: 22px;
    overflow: hidden;
    background: linear-gradient(160deg, var(--card-white) 40%, var(--card-grey) 100%);
  }
  .brand-band {
    position: absolute;
    left: 0;
    top: 0;
    width: 262px;
    height: 100%;
    background: linear-gradient(175deg, var(--band-light) 0%, var(--band-deep) 100%);
  }
  .band-brand {
    position: absolute;
    top: 78px;
    left: 0;
    width: 100%;
    display: flex;
    align-items: center;
    justify-content: center;
    gap: 10px;
  }
  .band-dot {
    width: 16px;
    height: 16px;
    border-radius: 50%;
    background: var(--dot-fill);
  }
  .band-name {
    font-size: 21px;
    font-weight: 700;
    color: var(--band-text);
    letter-spacing: 0.3px;
  }
  .card-body {
    position: absolute;
    left: 300px;
    top: 0;
    right: 40px;
    height: 100%;
  }
  .company-name {
    position: absolute;
    top: 34px;
    left: 0;
    font-size: 40px;
    font-weight: 700;
    color: var(--brand-bronze);
    white-space: nowrap;
  }
  .person {
    position: absolute;
    top: 206px;
    left: 0;
  }
  .person-name {
    font-size: 36px;
    font-weight: 400;
    color: var(--text-main);
    line-height: 1.1;
  }
  .person-credentials {
    font-size: 24px;
    color: var(--text-main);
    margin-top: 6px;
  }
  .contact {
    position: absolute;
    top: 356px;
    left: 0;
    font-size: 23px;
    color: var(--text-soft);
    line-height: 1.55;
    list-style: none;
    white-space: nowrap;
  }
</style>
</head>
<body>
  <main class="canvas">
    <article class="business-card">
      <div class="brand-band">
        <div class="band-brand">
          <span class="band-dot" aria-hidden="true"></span>
          <span class="band-name">Vesta Advisory</span>
        </div>
      </div>
      <div class="card-body">
        <h1 class="company-name">Vesta Advisory LTD</h1>
        <div class="person">
          <p class="person-name">Rebecca Thornbury</p>
          <p class="person-credentials">CA, BMS (Hons)</p>
        </div>
        <ul class="contact">
          <li class="contact-phone">PH +64 21 574 613</li>
          <li class="contact-email">r.thornbury@vestaadvisory.co.nz</li>
        </ul>
      </div>
    </article>
  </main>
</body>
</html>
```